The Vantor Codex Book Cover

"The Vantor Codex" is a book I wrote with the slogan "Unlock Performance, Spark Engagement: Master the Art of Building Winning Cultures in Today's Hybrid World". The book is designed around a methodology that's mine and that I attached. I would love to see the graphic of the methodology integrated in the design in a very subtle way. Use colors from the model but the book cover should be catchy, modern and engaging to the eye.
Overall the book is about three key elements towards success:
- (Self) Directions (purpose)
- Human experience (people and psychological safety)
- Maximize engagement
The methodology is a FLOW so flow is something that could be incorporated as well in the concept.
Low design quality
Managers and Teams

```html
<!DOCTYPE html>
<html lang="en">
<head>
<meta charset="utf-8">
<title>The Vantor Codex – Book Cover</title>
<link rel="stylesheet" href="https://fonts.googleapis.com/css2?family=Playfair+Display:ital,wght@0,900;1,900&family=Montserrat:wght@700&family=Oswald:wght@500&family=Josefin+Sans:wght@300&display=swap">
<style>
  :root {
    --ink: #0d0d0d;
    --teal: #2c8696;
    --paper: #ffffff;
    --flow-magenta: #b04a9e;
    --flow-indigo: #3c3f9a;
    --flow-gold: #f2c040;
    --flow-lime: #bfc23a;
    --flow-aqua: #1fb3b4;
    --flow-red: #e8465a;
  }
  html, body {
    margin: 0;
    padding: 0;
    overflow: hidden;
    background: var(--paper);
  }
  .cover {
    position: relative;
    width: 933px;
    height: 1200px;
    overflow: hidden;
    background: var(--paper);
    color: var(--ink);
  }
  .tagline {
    position: absolute;
    top: 24px;
    margin: 0;
    font-family: "Montserrat", sans-serif;
    font-weight: 700;
    font-size: 13px;
    letter-spacing: 0.32em;
    line-height: 1;
    text-transform: uppercase;
  }
  .tagline--left { left: 88px; }
  .tagline--right { left: 537px; }
  .title {
    margin: 0;
    font-family: "Playfair Display", serif;
    font-weight: 900;
  }
  .title span {
    position: absolute;
    left: 0;
    width: 100%;
    text-align: center;
    line-height: 1;
  }
  .title__article {
    top: 6px;
    font-style: italic;
    font-size: 76px;
    letter-spacing: -0.02em;
    color: var(--ink);
  }
  .title__main {
    top: 84px;
    font-size: 188px;
    letter-spacing: -0.03em;
    color: var(--ink);
  }
  .title__second {
    top: 256px;
    font-size: 160px;
    letter-spacing: -0.02em;
    color: var(--teal);
  }
  .subtitle {
    position: absolute;
    top: 466px;
    left: 0;
    width: 100%;
    margin: 0;
    text-align: center;
    font-family: "Oswald", sans-serif;
    font-weight: 500;
    font-size: 32px;
    line-height: 44px;
    text-transform: uppercase;
    letter-spacing: 0.005em;
  }
  .flow-art {
    position: absolute;
    left: 100px;
    top: 585px;
    width: 780px;
    height: 470px;
  }
  .author {
    position: absolute;
    top: 1112px;
    left: 0;
    width: 100%;
    margin: 0;
    text-align: center;
    font-family: "Josefin Sans", sans-serif;
    font-weight: 300;
    font-size: 48px;
    letter-spacing: 0.55em;
    text-indent: 0.55em;
    line-height: 1;
    text-transform: uppercase;
  }
</style>
</head>
<body>
  <main class="cover">
    <p class="tagline tagline--left">Unlock Performance,</p>
    <p class="tagline tagline--right">Spark Engagement:</p>

    <h1 class="title">
      <span class="title__article">The</span>
      <span class="title__main">Vantor</span>
      <span class="title__second">Codex</span>
    </h1>

    <p class="subtitle">Master the art of building winning<br>cultures in today's hybrid world</p>

    <svg class="flow-art" viewBox="0 0 780 470" role="img" aria-label="Illustration of the flow methodology: a colourful circular model with team figures over a faint network globe, joined by a looping arrow to a compass">
      <defs>
        <linearGradient id="flowTones" x1="0" y1="0" x2="1" y2="1">
          <stop offset="0" stop-color="var(--flow-red)"/>
          <stop offset="0.3" stop-color="var(--flow-magenta)"/>
          <stop offset="0.5" stop-color="var(--flow-indigo)"/>
          <stop offset="0.7" stop-color="var(--flow-aqua)"/>
          <stop offset="1" stop-color="var(--flow-lime)"/>
        </linearGradient>
        <radialGradient id="flowFade" cx="0.5" cy="0.5" r="0.5">
          <stop offset="0.55" stop-color="#fff" stop-opacity="0"/>
          <stop offset="1" stop-color="#fff" stop-opacity="1"/>
        </radialGradient>
      </defs>
      <rect x="0" y="0" width="780" height="470" rx="235" fill="url(#flowTones)" opacity="0.85"/>
      <rect x="0" y="0" width="780" height="470" rx="235" fill="url(#flowFade)"/>
    </svg>

    <p class="author">Author Name</p>
  </main>
</body>
</html>
```